New Website for novelty yarn producer

We need a new website for our company, Vedrana. We make highly tailored yarns for weavers worldwide. This year marks our 40th anniversary and we want to evolve our image and identity.

Our temporary website can be found at:
www.vedranathreads.example

Our only concern in that throughout the website the protagonist must be our client, we make their creations possible and are highly adaptable both during the ideation process of the yarn as well as in the production. This is at the core of the way we do business and is summarised within the concept of FMC (Full Motion Craft).

Industry/Entity Type

Textile

Number of Pages Required

1 page

Colors
9bcb3c

Requirements
Must have
• Full Motion Craft (FMC) - can be found on or current website www.vedranathreads.example

```html
<!DOCTYPE html>
<html lang="en">
<head>
<meta charset="utf-8">
<title>Vedrana — Novelty Yarn Solutions</title>
<link href="https://fonts.googleapis.com/css2?family=Oranienbaum&family=Open+Sans:wght@400;600;700&family=Roboto+Condensed:wght@400;700&display=swap" rel="stylesheet">
<style>
:root{
  --green:#9bcb3c;
  --ink:#1a1a1a;
  --text:#555;
  --grey-bg:#f4f4f4;
  --header-grey:#e2e1e1;
  --dark:#2a2a2a;
  --white:#fff;
  --serif:"Oranienbaum", "Times New Roman", serif;
  --sans:"Open Sans", Arial, sans-serif;
  --cond:"Roboto Condensed", Arial, sans-serif;
}
*{box-sizing:border-box;margin:0;padding:0}
html,body{width:1200px;height:2786px;overflow:hidden}
body{position:relative;background:var(--white);font-family:var(--sans);color:var(--ink)}
.abs{position:absolute}
.narrow{display:inline-block;white-space:nowrap;transform:scaleX(.7);transform-origin:left top}

/* header */
.header-block{left:0;top:0;width:509px;height:122px;background:var(--header-grey)}
.brand{left:230px;top:32px;font-family:var(--sans);font-weight:600;font-size:36px;line-height:1;letter-spacing:1px;color:var(--ink)}
.nav{left:550px;top:28px;display:flex;gap:24px;font-family:var(--cond);font-size:12px;font-weight:700}
.nav a{color:var(--ink);text-decoration:none}
.nav a.active{color:var(--green)}

/* hero */
.hero-photo{left:427px;top:61px;width:773px;height:444px;background:linear-gradient(120deg,#9a948c 0%,#c9b7aa 40%,#d8a79a 65%,#b98579 100%)}
.hero-card{left:0;top:122px;width:509px;height:335px;background:var(--white);box-shadow:0 2px 14px rgba(0,0,0,.12);padding:58px 0 0 230px}
.hero-title{font-family:var(--serif);font-weight:400;font-size:80px;line-height:80px;text-transform:uppercase;letter-spacing:1px;height:160px}
.hero-title .narrow{transform:scaleX(.64)}
.hero-text{font-size:11px;line-height:1.7;color:var(--text);margin-top:14px;width:250px}
.dash{top:482px;width:22px;height:3px;background:#444}
.dash.on{background:var(--green);width:24px}

/* values */
.value{width:172px;height:172px;transform:rotate(45deg);border:4px solid var(--white);box-shadow:0 2px 12px rgba(0,0,0,.25);overflow:hidden}
.value-fill{width:100%;height:100%}
.value-body{width:190px;text-align:center;color:var(--white)}
.value-title{font-size:16px;font-weight:600}
.value-text{font-size:9.5px;font-weight:600;line-height:1.55;margin:8px auto 12px;width:150px}
.btn-ghost{display:inline-block;border:1px solid var(--white);font-size:9px;font-weight:700;padding:7px 8px;color:var(--white)}

/* approach */
.approach{left:230px;top:901px;width:738px;height:473px;background:var(--grey-bg);text-align:center}
.approach-title{font-family:var(--serif);font-weight:400;font-size:50px;line-height:52px;margin-top:46px;height:104px}
.approach-title .narrow{transform:scaleX(.72);transform-origin:center top}
.approach-sub{font-size:12.5px;font-weight:700;letter-spacing:.5px;margin-top:12px;color:#333}
.approach-text{font-size:10.5px;line-height:1.8;color:var(--text);width:640px;margin:14px auto 0}
.btn{display:inline-block;border:1px solid var(--ink);font-size:11px;font-weight:700;padding:11px 14px;background:var(--white);color:var(--ink)}
.approach .btn{margin-top:20px}
.approach-photo{left:405px;top:1248px;width:416px;height:238px;background:var(--white);padding:8px;box-shadow:0 3px 12px rgba(0,0,0,.3)}
.approach-photo div{width:100%;height:100%;background:linear-gradient(135deg,#3b3d40,#5f6a6b 55%,#3a3a3c)}

/* team band */
.band{left:0;top:1575px;width:1200px;height:483px;background:linear-gradient(100deg,#3a2e2c 0%,#6a2a36 35%,#4e4543 65%,#7a6a5a 100%)}
.band-name{left:96px;top:1820px;font-family:var(--sans);font-weight:600;font-size:104px;line-height:1;color:var(--white)}
.team-card{left:631px;top:1709px;width:342px;height:378px;background:var(--white);padding:52px 24px 0 28px;box-shadow:0 2px 10px rgba(0,0,0,.2)}
.team-text{font-size:12.5px;font-weight:600;line-height:28.5px;letter-spacing:.3px;text-transform:uppercase;color:var(--ink)}
.team-card .btn{margin-top:14px;font-size:10px;font-weight:600;padding:10px 16px}

/* numbers */
.num-head{left:230px;top:2145px}
.num-mark{width:2px;height:14px;background:var(--ink)}
.num-title{font-family:var(--serif);font-weight:400;font-size:42px;line-height:44px;margin-top:6px;height:44px}
.num-text{font-size:10.5px;font-weight:600;line-height:1.7;color:#444;width:360px;margin-top:6px}
.num-link{font-size:10px;font-weight:700;margin-top:12px}
.num-link span{color:var(--green)}
.grey-strip{background:var(--grey-bg)}
.photo-fill{background:linear-gradient(160deg,#b9b9b9,#7a7e86)}
.stat-value{font-size:34px;font-weight:600;color:var(--green);line-height:1}
.stat-label{font-size:13px;font-weight:600;color:#333;margin-top:6px;text-transform:uppercase}
.stat-link{font-size:9.5px;font-weight:700;text-decoration:underline;margin-top:6px}
.plus{left:500px;top:2367px;width:34px;height:34px}

/* footer */
.footer{left:0;top:2546px;width:1200px;height:206px;background:var(--dark);color:var(--white)}
.foot-head{font-size:12px;font-weight:700;letter-spacing:.5px}
.foot-list{list-style:none;font-size:10.5px;line-height:2}
.foot-list li::before{content:"→ ";color:var(--green)}
.foot-rule{width:1px;background:#777}
.email{left:810px;top:2651px;width:160px;height:30px;border:1px solid #bbb;font-size:10px;padding:8px 10px}
.copyright{left:0;top:2752px;width:1200px;height:34px;background:var(--green);color:var(--white);font-size:10px;text-align:center;line-height:34px}
</style>
</head>
<body>

<header>
  <div class="abs header-block"></div>
  <div class="abs brand">Vedrana</div>
  <nav class="abs nav">
    <a class="active" href="#">Home</a><a href="#">About us</a><a href="#">Full Motion Craft</a><a href="#">Heritage</a><a href="#">Team</a><a href="#">Blog</a><a href="#">Contact</a>
  </nav>
</header>

<section>
  <div class="abs hero-photo" role="img" aria-label="Close-up photo of wound skeins of grey and pink yarn"></div>
  <div class="abs hero-card">
    <h1 class="hero-title"><span class="narrow">Tailored Weaving<br>Solutions</span></h1>
    <p class="hero-text">Versatility and flexibility both in development and production are key in delivering..</p>
  </div>
  <div class="abs dash" style="left:230px"></div>
  <div class="abs dash" style="left:266px"></div>
  <div class="abs dash on" style="left:303px"></div>
</section>

<section>
  <div class="abs value" style="left:267px;top:614px"><div class="value-fill" role="img" aria-label="Photo of colourful yarn bundles in green, teal and crimson" style="background:linear-gradient(135deg,#4a6b3a,#2f4a5a 50%,#7a1e3a)"></div></div>
  <div class="abs value-body" style="left:258px;top:645px">
    <div class="value-title">Experience</div>
    <div class="value-text">Over the years the company has gained the knowledge and skills that define the superiority of our...</div>
    <span class="btn-ghost">Learn More</span>
  </div>

  <div class="abs value" style="left:484px;top:614px"><div class="value-fill" role="img" aria-label="Photo of woven fabric in slate and plum tones" style="background:linear-gradient(135deg,#45455a,#5a4a55 50%,#3a3d48)"></div></div>
  <div class="abs value-body" style="left:475px;top:645px">
    <div class="value-title">Creativity</div>
    <div class="value-text">Our belief is that the key to our clients' success is a combination of innovation, creativity and quality</div>
    <span class="btn-ghost">Learn More</span>
  </div>

  <div class="abs value" style="left:703px;top:614px"><div class="value-fill" role="img" aria-label="Photo of dark textured fabric with golden thread" style="background:linear-gradient(135deg,#2a2a2a,#3e3a30 55%,#222)"></div></div>
  <div class="abs value-body" style="left:694px;top:645px">
    <div class="value-title">Professionality</div>
    <div class="value-text">We are a family business at the core. Our company is run with the same values as the Marelli family</div>
    <span class="btn-ghost">Learn More</span>
  </div>
</section>

<section>
  <div class="abs approach">
    <h2 class="approach-title"><span class="narrow">VNYS Full Motion<br>Craft</span></h2>
    <div class="approach-sub">PRODUCTION BUILT AROUND YOU</div>
    <p class="approach-text">We believe that the key to delivering a yarn that exceeds our client's expectation is to work together with weavers from step one, starting from the desired end product and working backwards. This allows us to develop the product that our weavers need, rather than having weavers adapt to the supplied raw materials.</p>
    <span class="btn">FIND OUT MORE</span>
  </div>
  <div class="abs approach-photo"><div role="img" aria-label="Photo of hands holding balls of pale blue yarn"></div></div>
</section>

<section>
  <div class="abs band" role="img" aria-label="Photo of a loom with crimson warp threads and coloured yarn on a table"></div>
  <div class="abs band-name">Vedrana</div>
  <div class="abs team-card">
    <p class="team-text">Our team has decades of experience in providing yarn solutions to weavers around the world, assisting them in the creation of outstanding textiles. Our clients can expect open lines of communication, clarity and professionality. Your focus is our client. The success of a client is our success.</p>
    <span class="btn">OUR HERITAGE</span>
  </div>
</section>

<section>
  <div class="abs num-head">
    <div class="num-mark"></div>
    <h2 class="num-title"><span class="narrow">VNYS in Numbers</span></h2>
    <p class="num-text">VNYS COMBINES THE EXPERIENCE OF A TEAM THAT HAS SERVED THE WEAVING INDUSTRY FOR OVER 40 YEARS</p>
    <div class="num-link">FIND OUR MORE <span>→</span></div>
  </div>

  <div class="abs grey-strip" style="left:602px;top:2162px;width:598px;height:148px"></div>
  <div class="abs photo-fill" style="left:602px;top:2162px;width:171px;height:148px" role="img" aria-label="Portrait photo of a team member"></div>
  <div class="abs" style="left:793px;top:2200px">
    <div class="stat-value">2</div>
    <div class="stat-label">Million kilograms/ yr</div>
    <div class="stat-link">LEARN MORE</div>
  </div>

  <div class="abs grey-strip" style="left:0;top:2310px;width:431px;height:149px"></div>
  <div class="abs" style="left:295px;top:2345px">
    <div class="stat-value">40</div>
    <div class="stat-label">Years in business</div>
    <div class="stat-link">LEARN MORE</div>
  </div>
  <div class="abs photo-fill" style="left:431px;top:2310px;width:171px;height:149px;background:linear-gradient(160deg,#c8c8c8,#8d8d95)" role="img" aria-label="Portrait photo of a team member"></div>
  <div class="abs" style="left:455px;top:2320px;width:125px;height:129px;background:rgba(255,255,255,.35)"></div>
  <svg class="abs plus" viewBox="0 0 34 34" aria-hidden="true"><path d="M17 9v16M9 17h16" stroke="#111" stroke-width="3"/></svg>
  <div class="abs" style="left:622px;top:2345px">
    <div class="stat-value">8</div>
    <div class="stat-label">Brands</div>
    <div class="stat-link">LEARN MORE</div>
  </div>
  <div class="abs" style="left:773px;top:2310px;width:195px;height:149px;background:linear-gradient(135deg,#b34a55,#7a2a3a 50%,#c98a7a)" role="img" aria-label="Photo of stacked patterned fabric swatches"></div>
</section>

<footer>
  <div class="abs footer"></div>
  <div class="abs foot-head" style="left:230px;top:2596px;color:#fff">USEFUL LINKS</div>
  <ul class="abs foot-list" style="left:230px;top:2626px;color:#fff">
    <li>Home</li><li>About Us</li><li>Full Motion Craft</li><li>Heritage</li>
  </ul>
  <div class="abs foot-rule" style="left:390px;top:2630px;height:66px"></div>
  <ul class="abs foot-list" style="left:428px;top:2626px;color:#fff">
    <li>Team</li><li>Blog</li><li>Contact</li><li>Privacy Policy</li>
  </ul>
  <div class="abs foot-rule" style="left:560px;top:2630px;height:66px"></div>
  <div class="abs foot-head" style="left:589px;top:2596px;color:#fff">CONTACT US</div>
  <div class="abs" style="left:589px;top:2630px;font-size:10.5px;line-height:2;color:#fff">
    0555 010 234<br>Via dei Telai 12 - 50100<br>Borgo Lana - Italy<br>commerciale@vedrana.example
  </div>
  <div class="abs foot-head" style="left:810px;top:2596px;color:#fff">NEWSLETTER</div>
  <div class="abs email" style="color:#fff">Email</div>
  <svg class="abs" style="left:940px;top:2657px" width="18" height="18" viewBox="0 0 18 18" aria-hidden="true"><path d="M2 9 16 2 12 16 9 10z" fill="none" stroke="#fff" stroke-width="1.3"/></svg>
  <div class="abs copyright">© Copyright 2018 vedranathreads. All Rights Reserved.</div>
</footer>

</body>
</html>
```